Vantoq Business Card Project showing the logo and a marbo image on the rear

Design a whacky but professional business card, the logo is for the front and the Marbo image is for the rear. Happy to consider other open source Marbo Images if the designer wants to select one from the web. Vantoq is a competitor to OMB.com.au and Pellory.com.au and is based around every property in Australia

Target Market(s)

Business

Contact Information for Business Card

Name, Title, Email, Web, Phone Number

Font styles to use
Other font styles liked:
• avenir

Requirements
Must have
• Image on Back logo on front
Nice to have
• Happy to consider other images on rear, preftably Colin Marbo. Image supplied I own, we can use open source other Marbo Images

```html
<!DOCTYPE html>
<html lang="en">
<head>
<meta charset="utf-8">
<title>Vantoq Business Card</title>
<link rel="stylesheet" href="https://fonts.googleapis.com/css2?family=Nunito+Sans:wght@400;600;800&display=swap">
<style>
  :root {
    --stage: #1f1f1f;
    --card-dark: #1d1d1d;
    --orange: #f08a1c;
    --white: #ffffff;
    --soft-white: #e9e9e9;
    --sky: #3f7fd8;
    --sky-light: #5fb0ea;
    --city-red: #e2483a;
    --city-yellow: #f3c21f;
    --city-green: #2f7d3a;
    --city-teal: #23a7c4;
  }
  * { margin: 0; padding: 0; box-sizing: border-box; }
  html, body {
    width: 1200px; height: 988px; overflow: hidden;
    background: var(--stage);
    font-family: "Nunito Sans", "Avenir", sans-serif;
  }
  .canvas { position: relative; width: 1200px; height: 988px; }

  .card {
    position: absolute; width: 560px; height: 320px;
    border-radius: 18px; overflow: hidden;
    box-shadow: 0 18px 40px rgba(0,0,0,.55);
  }

  /* rear: artwork side */
  .card-art { left: 80px; top: 110px; }
  .art-fill {
    position: absolute; inset: 0;
    background:
      linear-gradient(180deg, rgba(95,176,234,.0) 0%, rgba(95,176,234,0) 40%, rgba(0,0,0,.05) 100%),
      linear-gradient(100deg, var(--sky-light) 0%, var(--sky) 30%, var(--city-green) 48%, var(--city-yellow) 62%, var(--orange) 74%, var(--city-red) 86%, var(--city-teal) 100%);
  }
  .art-logo {
    position: absolute; left: 0; right: 0; top: 50%;
    transform: translateY(-50%);
    display: flex; justify-content: center; align-items: center; gap: 14px;
  }

  .brand-mark { width: 34px; height: 34px; background: var(--orange); border-radius: 4px; }
  .brand-name {
    font-weight: 800; color: var(--white); letter-spacing: 1px; line-height: 1;
  }
  .art-logo .brand-name { font-size: 58px; }

  /* front: details side */
  .card-info { left: 560px; top: 540px; background: var(--card-dark); }
  .edge-tab {
    position: absolute; left: 0; top: 96px; width: 9px; height: 58px;
    background: var(--orange);
  }
  .person { position: absolute; left: 36px; top: 96px; }
  .person-name {
    color: var(--orange); font-weight: 800; font-size: 25px;
    letter-spacing: .5px; text-transform: uppercase; line-height: 1.05;
  }
  .person-title { color: var(--soft-white); font-size: 17px; font-weight: 400; margin-top: 2px; }

  .info-logo {
    position: absolute; right: 34px; top: 30px;
    display: flex; align-items: center; gap: 12px;
  }
  .info-logo .brand-name { font-size: 44px; }
  .info-logo .brand-mark { width: 28px; height: 28px; }

  .address {
    position: absolute; right: 34px; top: 176px; text-align: right;
    color: var(--soft-white); font-size: 15px; line-height: 1.3;
  }
  .divider {
    position: absolute; left: 36px; right: 34px; top: 222px;
    height: 1px; background: var(--orange);
  }
  .contacts {
    position: absolute; left: 36px; top: 232px; list-style: none;
    color: var(--soft-white); font-size: 15px; line-height: 1.45;
  }
  .contacts li { display: flex; align-items: center; gap: 10px; }
  .contacts svg { width: 12px; height: 12px; fill: var(--orange); flex: none; }
  .accent { color: var(--orange); }
</style>
</head>
<body>
<main class="canvas">

  <section class="card card-art">
    <div class="art-fill" role="img" aria-label="Colourful pop-art city illustration in the Colin Marbo style: playful buildings, sun, clouds and stars"></div>
    <div class="art-logo">
      <span class="brand-mark"></span>
      <span class="brand-name">Vantoq</span>
    </div>
  </section>

  <section class="card card-info">
    <div class="edge-tab"></div>

    <div class="info-logo">
      <span class="brand-mark"></span>
      <span class="brand-name">Vantoq</span>
    </div>

    <div class="person">
      <p class="person-name">Daniel Harlow</p>
      <p class="person-title">Executive Producer</p>
    </div>

    <address class="address" style="font-style:normal">
      1400 W Arden Street<br>
      halston County name 5231
    </address>

    <div class="divider"></div>

    <ul class="contacts">
      <li>
        <svg viewBox="0 0 24 24" aria-hidden="true"><path d="M6.6 10.8a15 15 0 0 0 6.6 6.6l2.2-2.2c.3-.3.7-.4 1-.2 1.1.4 2.3.6 3.6.6.6 0 1 .4 1 1V20c0 .6-.4 1-1 1A17 17 0 0 1 3 4c0-.6.4-1 1-1h3.5c.6 0 1 .4 1 1 0 1.3.2 2.5.6 3.6.1.3 0 .7-.2 1z"/></svg>
        555-210-4471
      </li>
      <li>
        <svg viewBox="0 0 24 24" aria-hidden="true"><path d="M2 5h20v14H2zM4 7v.5l8 5 8-5V7l-8 5z"/></svg>
        Daniel@vantoq.com.au
      </li>
      <li>
        <svg viewBox="0 0 24 24" aria-hidden="true"><path d="M12 2a10 10 0 1 0 0 20 10 10 0 0 0 0-20zm0 2.2c.9 1.1 1.6 2.7 2 4.6h-4c.4-1.9 1.1-3.5 2-4.6zM4.6 10.8h3.3a17 17 0 0 0 0 2.4H4.6a7.8 7.8 0 0 1 0-2.4zm5.3 0h4.2a15 15 0 0 1 0 2.4H9.9a15 15 0 0 1 0-2.4zm6.2 0h3.3a7.8 7.8 0 0 1 0 2.4h-3.3a17 17 0 0 0 0-2.4zM12 19.8c-.9-1.1-1.6-2.7-2-4.6h4c-.4 1.9-1.1 3.5-2 4.6z"/></svg>
        <span>www.<span class="accent">vantoq</span>.com.au</span>
      </li>
    </ul>
  </section>

</main>
</body>
</html>
```